New, modern business card for growing audiology practice

We need a new business card for our audiology practice. Our logo and website have recently changed (more modern) and we want our business cards to reflect this change.
We conduct hearing tests, perform earwax removals, and fit & dispense hearing aids to our patients. We are a family owned practice in which the owner is the one who works directly with the patient. I have attached logos in various formats to use, as well as two ideas I found on this website; as well as a scanned copy of our current logo. Good luck!

Industry/Entity Type

Business

Contact Information for Business Card

Company name: Tolvera Hearing Center
Provider name: Peter Wolstenby, Au.D. F/NSB
Phone number: (440) 683-5127
Address: 837 W. Lindell Ave. Brenford Falls, OH 44087
email: tolverahearing@postvane.com
website: tolverahearing.com

Colors
000000
aaaaaa
dbdbdb
cacaca
9bcb3c
afd23c
cadf82
b1b1b1

Requirements
Must have
• My card must include information in the "details" section. In the attached images, I found a few that I liked and I would like to model after - "brisky bouncin'" and "Sound Method Center".
• Must be horizontal.
• Must include logos provided. I uploaded them in various file formats and various ways.
• Must match logo font, if possible, if not, please get as close as you can.
Nice to have
• I really like the idea of having a color on one side with just the logo and company name and the contact information and provider name on the other side. I also really like the idea of having the main color dominating on the logo/company side with accent of that same color on the contact side of the card.
Should not have
• Must not be vertical.

```html
<!DOCTYPE html>
<html lang="en">
<head>
<meta charset="utf-8">
<title>Tolvera Hearing Center – Business Card</title>
<link rel="stylesheet" href="https://fonts.googleapis.com/css2?family=Montserrat:wght@300;400;500&display=swap">
<style>
  :root {
    --ink: #0b0b0b;
    --card: #111111;
    --stage: #2a2a2a;
    --lime: #9bcb3c;
    --lime-bright: #afd23c;
    --white: #f4f4f4;
    --grey: #b1b1b1;
    --grey-soft: #aaaaaa;
  }
  * { box-sizing: border-box; margin: 0; padding: 0; }
  html, body { width: 1200px; height: 900px; overflow: hidden; }
  body {
    background: var(--stage);
    font-family: "Montserrat", Arial, sans-serif;
    color: var(--white);
    display: flex;
    flex-direction: column;
    align-items: center;
    justify-content: center;
    gap: 36px;
  }
  .card {
    position: relative;
    width: 720px;
    height: 400px;
    border-radius: 20px;
    background: linear-gradient(160deg, #1a1a1a 0%, var(--card) 55%, var(--ink) 100%);
    overflow: hidden;
  }

  .brand { display: flex; align-items: center; gap: 12px; }
  .brand-dot { width: 16px; height: 16px; border-radius: 50%; background: var(--lime); flex: none; }
  .brand-name {
    font-weight: 400;
    text-transform: uppercase;
    letter-spacing: 0.04em;
    color: var(--white);
    font-size: 19px;
    white-space: nowrap;
  }

  .contact-side .brand { position: absolute; top: 54px; right: 60px; }
  .contact-side .divider {
    position: absolute; left: 60px; right: 60px; top: 170px;
    height: 1px; background: var(--lime);
  }
  .provider { position: absolute; left: 60px; top: 196px; }
  .provider-name {
    font-size: 25px; font-weight: 500; color: var(--lime-bright);
    text-transform: uppercase; letter-spacing: 0.01em;
  }
  .provider-role { font-size: 16px; font-weight: 300; color: var(--grey); margin-top: 4px; }
  .contact-list { position: absolute; left: 60px; top: 270px; list-style: none; }
  .contact-list li {
    display: flex; align-items: center; gap: 12px;
    font-size: 16px; font-weight: 300; color: var(--white); line-height: 26px;
  }
  .contact-list svg { width: 13px; height: 13px; flex: none; }
  .accent { color: var(--lime-bright); }
  .address {
    position: absolute; right: 60px; top: 270px;
    text-align: right; font-size: 15px; font-weight: 300; font-style: normal;
    color: var(--grey-soft); line-height: 24px;
  }
  .footer-band {
    position: absolute; left: 0; right: 0; bottom: 0; height: 28px;
    background: var(--lime); border-top: 3px solid var(--white);
  }

  .logo-side .brand { position: absolute; left: 50%; top: 150px; transform: translateX(-50%); gap: 16px; }
  .logo-side .brand-dot { width: 24px; height: 24px; }
  .logo-side .brand-name { font-size: 32px; }
  .web-rule {
    position: absolute; right: 70px; bottom: 86px;
    display: flex; align-items: center; gap: 12px;
    font-size: 13px; font-weight: 400; color: var(--white); letter-spacing: 0.02em;
  }
  .web-rule .line { width: 80px; height: 2px; background: var(--lime); }
</style>
</head>
<body>

  <section class="card contact-side" aria-label="Contact side">
    <div class="brand">
      <span class="brand-dot"></span>
      <span class="brand-name">Tolvera Hearing Center</span>
    </div>
    <div class="divider"></div>
    <div class="provider">
      <h1 class="provider-name">Peter Wolstenby, Au.D. F/NSB</h1>
      <p class="provider-role">Owner-Audiologist</p>
    </div>
    <ul class="contact-list">
      <li>
        <svg viewBox="0 0 16 16" aria-hidden="true"><path fill="#9bcb3c" d="M3.6 1.2l2.2 2.6-1.3 1.6c.9 2.3 2.6 4 4.9 5l1.6-1.3 2.6 2.2-1.4 2.5C6.6 13.6 2.4 9.4 1.2 3.8z"/></svg>
        (440) 683-5127
      </li>
      <li>
        <svg viewBox="0 0 16 16" aria-hidden="true"><rect x="1.5" y="3.5" width="13" height="9" fill="none" stroke="#9bcb3c" stroke-width="1.6"/><path d="M1.5 3.5L8 9l6.5-5.5" fill="none" stroke="#9bcb3c" stroke-width="1.6"/></svg>
        tolverahearing@postvane.com
      </li>
      <li>
        <svg viewBox="0 0 16 16" aria-hidden="true"><circle cx="8" cy="8" r="6.5" fill="none" stroke="#9bcb3c" stroke-width="1.5"/><ellipse cx="8" cy="8" rx="2.8" ry="6.5" fill="none" stroke="#9bcb3c" stroke-width="1.2"/><path d="M1.5 8h13" stroke="#9bcb3c" stroke-width="1.2"/></svg>
        <span>www.<span class="accent">tolverahearing</span>.com</span>
      </li>
    </ul>
    <address class="address">
      837 W. Lindell Ave.<br>
      Brenford Falls, OH 44087
    </address>
    <div class="footer-band"></div>
  </section>

  <section class="card logo-side" aria-label="Logo side">
    <div class="brand">
      <span class="brand-dot"></span>
      <span class="brand-name">Tolvera Hearing Center</span>
    </div>
    <div class="web-rule">
      <span class="line"></span>
      <span>www.<span class="accent">tolverahearing</span>.com</span>
      <span class="line"></span>
    </div>
  </section>

</body>
</html>
```